Business Card Design

Hi I need a business card designed, we already have the business name logo artwork and would like some concept ideas for the Bus Card layout.
On the back of the card i want to include the products and services that we offer.
We are a Plastics Sheeting manufacture based in Perth Australia.

                                       

We need a BC design for a company called Tarvo Plastics based in Perth Australia.

We supply from DIY to Trade & Industrial  Engineering Markets.

We specialise in:

·         Cut to size panels  (all shapes and sizes)

·         Plastics fabrication & Welding

·         Custom Designs

·         Plastic Repairs

·         PVC Pipe Slotting & PVC Pipe Threading

·         Supplier of all types of engineering plastics and profiles.

Including:           Acrylic / Clarvene

                               Polycarbonate / Dorvil

                               Prismatic Light Diffuser

                               Vantrib

                               HDPE / UHMWPE

                               PVC / PVC Foam

                               Nylon

                               HIPS

```html
<!DOCTYPE html>
<html lang="en">
<head>
<meta charset="utf-8">
<title>Tarvo Plastics – Business Card</title>
<link href="https://fonts.googleapis.com/css2?family=Open+Sans:wght@400;600;700;800&display=swap" rel="stylesheet">
<style>
  :root{
    --navy:#1b2a5c;
    --orange:#e07a22;
    --amber:#f0a32a;
    --white:#ffffff;
    --stage:#eceef2;
    --rule:#8a93b3;
  }
  *{margin:0;padding:0;box-sizing:border-box}
  html,body{width:1200px;height:987px;overflow:hidden;background:var(--stage);font-family:"Open Sans",sans-serif}
  .card{position:absolute;width:600px;height:345px;border-radius:22px;overflow:hidden;box-shadow:0 6px 18px rgba(20,30,60,.18)}

  /* back */
  .card-back{left:540px;top:70px;background:var(--navy);color:var(--white)}
  .back-name{position:absolute;right:34px;top:26px;font-size:40px;font-weight:800;letter-spacing:-.5px}
  .back-lead{position:absolute;left:34px;right:34px;top:92px;text-align:center;font-size:15px;font-weight:700;font-style:italic;line-height:1.3}
  .col{position:absolute;top:148px}
  .col-services{left:30px;width:300px}
  .col-materials{left:350px;width:230px}
  .divider{position:absolute;left:334px;top:150px;width:1px;height:160px;background:var(--rule)}
  .col h3{color:var(--amber);font-size:17px;font-weight:700;margin-bottom:4px}
  .col ul{list-style:none}
  .col li{font-size:12.5px;line-height:1.38;padding-left:13px;position:relative}
  .col li::before{content:"";position:absolute;left:0;top:6px;width:6px;height:6px;border-radius:50%;background:var(--amber)}

  /* front */
  .card-front{left:60px;top:560px;background:var(--white)}
  .card-front svg{position:absolute;inset:0}
  .holder{position:absolute;left:250px;top:34px;font-size:17px;font-weight:700;color:var(--navy)}
  .holder .title{color:var(--orange);font-weight:400}
  .front-name{position:absolute;left:150px;top:80px;display:flex;align-items:center;gap:12px;font-size:50px;font-weight:800;color:var(--navy);letter-spacing:-.5px}
  .front-name .mark{width:22px;height:22px;background:var(--orange)}
  .contact{position:absolute;left:26px;bottom:18px;color:var(--white);font-size:13.5px;line-height:1.55}
</style>
</head>
<body>

<section class="card card-back">
  <div class="back-name">Tarvo Plastics</div>
  <p class="back-lead">The Products And Services That We Offer<br>Are Supplied From Diy To Trade &amp; Industrial Engineering Markets</p>
  <div class="col col-services">
    <h3>We specialise in:</h3>
    <ul>
      <li>Cut to size panels (all shapes and sizes)</li>
      <li>Plastics fabrication &amp; Welding</li>
      <li>Custom Designs</li>
      <li>Plastic Repairs</li>
      <li>PVC Pipe Slotting &amp; PVC Pipe Threading</li>
      <li>Supplier of all types of engineering plastics and profiles</li>
    </ul>
  </div>
  <div class="divider"></div>
  <div class="col col-materials">
    <h3>Including:</h3>
    <ul>
      <li>Acrylic / Clarvene</li>
      <li>Polycarbonate / Dorvil</li>
      <li>Prismatic Light Diffuser</li>
      <li>Vantrib</li>
      <li>HDPE / UHMWPE</li>
      <li>PVC / PVC Foam</li>
      <li>Nylon</li>
      <li>HIPS</li>
    </ul>
  </div>
</section>

<section class="card card-front">
  <svg width="600" height="345" viewBox="0 0 600 345" aria-hidden="true">
    <path d="M0 60 C 60 200 260 275 640 232 L640 360 L-10 360 Z" fill="var(--navy)"/>
    <path d="M16 0 L36 0 C 70 140 230 228 450 250 C 220 244 58 160 16 0 Z" fill="var(--orange)"/>
  </svg>
  <div class="holder">Your Name, <span class="title">Title</span></div>
  <div class="front-name"><span class="mark"></span>Tarvo Plastics</div>
  <div class="contact">
    Unit 4/18 Harlow Circuit Brenton Vale NT 0899<br>
    PO Box 2240 Brenton Vale DC NT 0898<br>
    &#9990; 08 9400 1100 &nbsp;|&nbsp; M 123-456-7890 &nbsp;|&nbsp; F 08 9400 1122<br>
    &#9993; sales@tarvoplastics.com.au | Kestrel Holdings Pty Ltd T/A Tarvo Plastics ABN: TBA
  </div>
</section>

</body>
</html>
```